International business needs business cards

Our company, DRV Ventures Inc. is in the business of supplying a range construction products with particular emphasis on CEMENT. We have developed our own brand - TORVAN SUPPLIES - with which to infiltrate the market. We are launching our brand of cement (TORVAN Type IS Cement) into the Caribbean which is unlike anything this market has ever seen. A monopoly has existed here for the past 60-odd years and the market has now opened to allow the importation of other brands and consumers are anxious and ready for change/improvement. We are very excited to be launching and want to make a great first impression. We will be conducting workshops and seminars (from government level to the hardware store owners) and we want our business card to give us the strong, confident introduction that we need.

Target Market(s)

construction; builders; engineers; home owners

Industry/Entity Type

Construction

Contact Information for Business Card

Marisol Depree
CEO
cell # 1 555 4180736
Ground floor,Lindell Plaza Suite 2734
George Town,Grand Cayman
Cayman Islands,KY1-4823
EMAIL: m.depree@drvventuresinc.example
web site drvventuresinc.example

COMPANY: skype info drv.ventures.example

second card
Yvette Brannock-Depree
CFO
CELL# 1 555 607 3941
George Town,Grand Cayman
Cayman Islands,KY1-4823
EMAIL: y.brannockdepree@drvventuresinc.example
website drvventuresinc.example

Requirements
Must have
• Business cards must display BOTH logos - DRV is the company and TORVAN is the brand.

```html
<!DOCTYPE html>
<html lang="en">
<head>
<meta charset="utf-8">
<title>DRV Ventures Inc. – Business Card</title>
<link rel="stylesheet" href="https://fonts.googleapis.com/css2?family=Open+Sans:wght@400;600;700&display=swap">
<style>
  :root {
    --backdrop: #2b2b2d;
    --card-white: #ffffff;
    --maroon: #7e141c;
    --ink: #1a1a1a;
    --crest-grey: #3a3a3c;
    --light-text: #ffffff;
  }
  * { margin: 0; padding: 0; box-sizing: border-box; }
  html, body {
    width: 1200px;
    height: 900px;
    overflow: hidden;
    background: var(--backdrop);
    font-family: "Open Sans", Arial, sans-serif;
  }
  .canvas {
    position: relative;
    width: 1200px;
    height: 900px;
  }
  .card {
    position: absolute;
    left: 250px;
    width: 700px;
    height: 400px;
    background: var(--card-white);
    overflow: hidden;
  }
  .card--back { top: 30px; }
  .card--front { top: 470px; display: flex; }

  /* Back: brand mark */
  .brand-mark {
    position: absolute;
    top: 130px;
    left: 0;
    width: 100%;
    display: flex;
    justify-content: center;
    align-items: center;
    gap: 16px;
  }
  .brand-mark__dot {
    width: 34px;
    height: 34px;
    border-radius: 50%;
    background: var(--crest-grey);
  }
  .brand-mark__name {
    font-size: 58px;
    font-weight: 700;
    letter-spacing: 6px;
    color: var(--crest-grey);
  }
  .handle {
    position: absolute;
    top: 318px;
    left: 0;
    width: 100%;
    display: flex;
    justify-content: center;
    align-items: center;
    gap: 8px;
    font-size: 17px;
    color: var(--ink);
  }
  .handle__dot {
    width: 16px;
    height: 16px;
    border-radius: 50%;
    background: var(--maroon);
  }

  /* Front: company mark + details */
  .front__logo-side {
    width: 34%;
    position: relative;
    background: var(--card-white);
  }
  .company-mark {
    position: absolute;
    top: 70px;
    left: 42px;
    display: flex;
    align-items: center;
    gap: 10px;
  }
  .company-mark__square {
    width: 52px;
    height: 52px;
    background: var(--maroon);
  }
  .company-mark__name {
    font-size: 20px;
    font-weight: 700;
    line-height: 1.1;
    color: var(--ink);
  }
  .front__details {
    width: 66%;
    background: var(--maroon);
    color: var(--light-text);
    padding: 92px 40px 0 46px;
  }
  .person__name {
    font-size: 27px;
    font-weight: 700;
    letter-spacing: 0.5px;
    line-height: 1.1;
  }
  .person__title {
    font-size: 14px;
    font-weight: 600;
    margin-bottom: 14px;
  }
  .address {
    font-size: 15px;
    line-height: 1.35;
    margin-bottom: 6px;
  }
  .contact-line {
    display: flex;
    align-items: center;
    gap: 8px;
    font-size: 15px;
    line-height: 1.45;
  }
  .contact-line svg {
    width: 12px;
    height: 12px;
    flex: none;
  }
</style>
</head>
<body>
<main class="canvas">

  <section class="card card--back" aria-label="Business card back">
    <div class="brand-mark">
      <span class="brand-mark__dot"></span>
      <span class="brand-mark__name">TORVAN</span>
    </div>
    <div class="handle">
      <span class="handle__dot"></span>
      <span>drv.ventures.example</span>
    </div>
  </section>

  <section class="card card--front" aria-label="Business card front">
    <div class="front__logo-side">
      <div class="company-mark">
        <span class="company-mark__square"></span>
        <span class="company-mark__name">DRV Ventures Inc.</span>
      </div>
    </div>
    <div class="front__details">
      <h1 class="person__name">MARISOL DEPREE</h1>
      <p class="person__title">CEO</p>
      <p class="address">
        Ground floor,Lindell Plaza Suite 2734<br>
        George Town,Grand Cayman<br>
        Cayman Islands,KY1-4823
      </p>
      <p class="contact-line">
        <svg viewBox="0 0 12 12" aria-hidden="true"><path d="M2.5 1 L4.5 1 L5 3.5 L3.8 4.4 Q4.8 6.6 7.6 8.2 L8.5 7 L11 7.5 L11 9.5 Q10 11 8.5 11 Q2 9 1 3.5 Q1 2 2.5 1Z" fill="#fff"/></svg>
        1 555 4180736
      </p>
      <p class="contact-line">
        <svg viewBox="0 0 12 12" aria-hidden="true"><rect x="0.8" y="2.5" width="10.4" height="7" fill="none" stroke="#fff" stroke-width="1.2"/><path d="M1 3 L6 6.8 L11 3" fill="none" stroke="#fff" stroke-width="1.2"/></svg>
        m.depree@drvventuresinc.example
      </p>
      <p class="contact-line">
        <svg viewBox="0 0 12 12" aria-hidden="true"><circle cx="6" cy="6" r="5" fill="none" stroke="#fff" stroke-width="1.1"/><ellipse cx="6" cy="6" rx="2.2" ry="5" fill="none" stroke="#fff" stroke-width="1"/><path d="M1 6 H11" stroke="#fff" stroke-width="1"/></svg>
        www.drvventuresinc.example
      </p>
    </div>
  </section>

</main>
</body>
</html>
```